Folder Design (inside and out) for a medical technology company

We are a Medical Technology company looking for a professional folder design.
Folder design is for Front, Back, and the flaps inside the folder. We've provided a variety of products at a national level for 20 years, we're targeting a demographic of doctors and are looking to improve out materials.

I attached our logo for reference, please feel free to reach out if you have any questions. Please use the pink and blue logo.

Thank you.

Target Market(s)

Doctors

Industry/Entity Type

Medical, Technology

Requirements
Must have
• Professional design

```html
<!DOCTYPE html>
<html lang="en">
<head>
<meta charset="utf-8">
<title>Helix Care – Presentation Folder</title>
<link rel="stylesheet" href="https://fonts.googleapis.com/css2?family=Montserrat:wght@400;500;700&display=swap">
<style>
  :root {
    --stage: #333335;
    --blue: #648dcd;
    --blue-deep: #5a83c4;
    --navy: #2b4e90;
    --pink: #e95b8a;
    --die-red: #e0485a;
    --die-blue: #2f4f97;
    --safe-green: #1aa34a;
    --paper: #f1f1f1;
    --white: #ffffff;
  }
  html, body {
    margin: 0;
    padding: 0;
    width: 1200px;
    height: 2346px;
    overflow: hidden;
    background: var(--stage);
  }
  .folder-sheet { display: block; width: 1200px; height: 2346px; }
  .brand-name { font-family: "Montserrat", sans-serif; font-weight: 700; font-size: 52px; }
  .contact-line { font-family: "Montserrat", sans-serif; font-weight: 500; font-size: 17px; fill: var(--white); }
  .pill-label { font-family: "Montserrat", sans-serif; font-weight: 700; fill: var(--white); }
  .tab-url { font-family: "Montserrat", sans-serif; font-weight: 500; font-size: 15px; fill: var(--white); }
  .headline { font-family: "Montserrat", sans-serif; font-weight: 700; font-size: 28px; fill: var(--pink); }
  .pocket-note { font-family: "Montserrat", sans-serif; font-weight: 400; font-size: 13px; fill: var(--white); }
  .die-cut { fill: none; stroke: var(--die-red); stroke-width: 3; }
  .die-inner { fill: none; stroke: var(--die-blue); stroke-width: 3; }
  .safe-line { fill: none; stroke: var(--safe-green); stroke-width: 2.5; stroke-dasharray: 7 5; }
  .fold-line { stroke: var(--die-red); stroke-width: 2; stroke-dasharray: 7 5; }
  .card-slit { stroke: var(--navy); stroke-width: 3; }
</style>
</head>
<body>
<svg class="folder-sheet" viewBox="0 0 1200 2346" xmlns="http://www.w3.org/2000/svg">
  <defs>
    <linearGradient id="heroFade" x1="0" y1="0" x2="0" y2="1">
      <stop offset="0" stop-color="#e3e9f5"/>
      <stop offset="0.55" stop-color="#bccbea"/>
      <stop offset="0.85" stop-color="#8aa8dc"/>
      <stop offset="1" stop-color="#648dcd"/>
    </linearGradient>
    <radialGradient id="heroGlow" cx="0.55" cy="0.45" r="0.55">
      <stop offset="0" stop-color="#ffffff" stop-opacity="0.85"/>
      <stop offset="0.5" stop-color="#dfe7f6" stop-opacity="0.5"/>
      <stop offset="1" stop-color="#dfe7f6" stop-opacity="0"/>
    </radialGradient>
    <radialGradient id="heroShade" cx="0.2" cy="0.3" r="0.45">
      <stop offset="0" stop-color="#9fb3dc" stop-opacity="0.7"/>
      <stop offset="1" stop-color="#9fb3dc" stop-opacity="0"/>
    </radialGradient>
    <radialGradient id="photoTone" cx="0.5" cy="0.45" r="0.6">
      <stop offset="0" stop-color="#d9c2ac"/>
      <stop offset="0.6" stop-color="#a9b97a"/>
      <stop offset="1" stop-color="#7c9a58"/>
    </radialGradient>
    <linearGradient id="innerPaper" x1="0" y1="0" x2="0" y2="1">
      <stop offset="0" stop-color="#f8f8f8"/>
      <stop offset="1" stop-color="#ebebec"/>
    </linearGradient>
    <radialGradient id="innerWash" cx="0.5" cy="0.5" r="0.5">
      <stop offset="0" stop-color="#dcdadb" stop-opacity="0"/>
      <stop offset="0.7" stop-color="#dcdadb" stop-opacity="0.55"/>
      <stop offset="1" stop-color="#dcdadb" stop-opacity="0"/>
    </radialGradient>
    <radialGradient id="pocketWash" cx="0.5" cy="0.2" r="0.7">
      <stop offset="0" stop-color="#e6e6e7"/>
      <stop offset="1" stop-color="#f8f8f8"/>
    </radialGradient>
    <linearGradient id="backBand" x1="0" y1="0" x2="1" y2="1">
      <stop offset="0" stop-color="#5f89cb"/>
      <stop offset="1" stop-color="#6d95d2"/>
    </linearGradient>
  </defs>

  <!-- ============ OUTSIDE ============ -->
  <g class="folder-outside">
    <rect class="panel-back" x="58" y="46" width="543" height="815" fill="url(#backBand)"/>
    <g class="hero-image" role="img" aria-label="Doctor with stethoscope holding a tablet surrounded by glowing medical icons">
      <rect x="58" y="46" width="543" height="430" fill="url(#heroFade)"/>
      <rect x="58" y="46" width="543" height="430" fill="url(#heroShade)"/>
      <rect x="58" y="46" width="543" height="430" fill="url(#heroGlow)"/>
    </g>
    <rect class="panel-front" x="601" y="46" width="546" height="815" fill="var(--paper)"/>
    <path class="pocket" d="M58 861 H1147 V1134 H660 Q644 1134 639 1112 L601 884 L563 1112 Q558 1134 542 1134 H58 Z" fill="var(--blue-deep)"/>

    <circle cx="196" cy="528" r="44" fill="var(--white)"/>
    <text class="brand-name" x="256" y="547" fill="var(--white)">Helix Care</text>

    <rect x="212" y="622" width="232" height="32" rx="16" fill="var(--pink)"/>
    <text class="pill-label" x="328" y="646" font-size="21" text-anchor="middle">CONTACT DETAILS</text>
    <g class="contact-icons" fill="var(--white)">
      <circle cx="295" cy="677" r="11"/>
      <circle cx="328" cy="677" r="11"/>
      <circle cx="361" cy="677" r="11"/>
      <path d="M295 683 C291 678 290 676 290 674 A5 5 0 0 1 300 674 C300 676 299 678 295 683 Z" fill="var(--blue)"/>
      <circle cx="295" cy="674" r="1.8" fill="var(--white)"/>
      <path d="M323 671 Q322 674 326 679 Q330 683 333 682 L334 680 L331 678 L329 679 Q326 677 325 674 L326 672 L324 670 Z" fill="var(--blue)"/>
      <rect x="355" y="672" width="12" height="9" rx="1.5" fill="var(--blue)"/>
      <path d="M355 673 L361 677 L367 673" fill="none" stroke="var(--white)" stroke-width="1.3"/>
    </g>
    <text class="contact-line" x="328" y="713" text-anchor="middle">Helix Care</text>
    <text class="contact-line" x="328" y="734" text-anchor="middle">2450 Harbor Point Blvd Ste 210</text>
    <text class="contact-line" x="328" y="755" text-anchor="middle">Lake Marin, FL 33100</text>
    <text class="contact-line" x="328" y="776" text-anchor="middle">800.555.0147</text>
    <text class="contact-line" x="328" y="797" text-anchor="middle">info@helixcaresupply.com</text>

    <path d="M184 861 V835 Q184 827 192 827 H459 Q467 827 467 835 V861 Z" fill="var(--pink)"/>
    <text class="tab-url" x="326" y="849" text-anchor="middle">www.helixcaresupply.com</text>

    <circle cx="728" cy="134" r="44" fill="var(--pink)"/>
    <text class="brand-name" x="790" y="153" fill="var(--blue)">Helix Care</text>

    <circle cx="875" cy="440" r="210" fill="var(--white)"/>
    <circle cx="875" cy="440" r="196" fill="url(#photoTone)" role="img" aria-label="Smiling senior couple embracing outdoors in a sunny park"/>

    <text class="headline" x="877" y="745" text-anchor="middle">THE MOST CONVENIENT WAY</text>
    <text class="headline" x="877" y="778" text-anchor="middle">TO GET YOUR DIABETIC</text>
    <text class="headline" x="877" y="811" text-anchor="middle">SUPPLIES</text>

    <path d="M735 861 V835 Q735 827 743 827 H1011 Q1019 827 1019 835 V861 Z" fill="var(--blue)"/>
    <text class="tab-url" x="877" y="849" text-anchor="middle">www.helixcaresupply.com</text>

    <line class="card-slit" x1="200" y1="958" x2="248" y2="911"/>
    <line class="card-slit" x1="428" y1="911" x2="476" y2="958"/>
    <line class="card-slit" x1="200" y1="1027" x2="248" y2="1073"/>
    <line class="card-slit" x1="428" y1="1073" x2="476" y2="1027"/>

    <g class="pocket-offers">
      <rect x="724" y="914" width="342" height="30" rx="15" fill="var(--pink)"/>
      <text class="pill-label" font-size="15" x="895" y="929" text-anchor="middle" dominant-baseline="central" transform="rotate(180 895 929)">VERIFY 1ST CGM SHIPMENT</text>
      <rect x="724" y="950" width="342" height="30" rx="15" fill="var(--pink)"/>
      <text class="pill-label" font-size="15" x="895" y="965" text-anchor="middle" dominant-baseline="central" transform="rotate(180 895 965)">DIABETIC SHOES</text>
      <rect x="724" y="988" width="342" height="30" rx="15" fill="var(--pink)"/>
      <text class="pill-label" font-size="15" x="895" y="1003" text-anchor="middle" dominant-baseline="central" transform="rotate(180 895 1003)">CONTINUOUS GLUCOSE MONITOR</text>
      <text class="pocket-note" x="895" y="1041" text-anchor="middle" dominant-baseline="central" transform="rotate(180 895 1041)">will cover your diabetic supplies</text>
      <text class="pocket-note" x="895" y="1058" text-anchor="middle" dominant-baseline="central" transform="rotate(180 895 1058)">to learn more and see if Medicare or your insurance</text>
      <text class="pocket-note" x="895" y="1075" text-anchor="middle" dominant-baseline="central" transform="rotate(180 895 1075)">NO OUT OF POCKET COST: Click on a product below</text>
    </g>

    <line class="fold-line" x1="601" y1="46" x2="601" y2="861"/>
    <line class="fold-line" x1="58" y1="861" x2="1147" y2="861"/>
    <path class="safe-line" d="M72 60 H1133 V1120 H666 Q652 1120 648 1104 L601 878 L554 1104 Q550 1120 536 1120 H72 Z"/>
    <path class="die-inner" d="M58 46 H1147 V1134 H660 Q644 1134 639 1112 L601 884 L563 1112 Q558 1134 542 1134 H58 Z"/>
    <path class="die-cut" d="M53 41 H1152 V1139 H660 Q640 1139 634 1115 L601 874 L568 1115 Q562 1139 542 1139 H53 Z"/>
  </g>

  <!-- ============ INSIDE ============ -->
  <g class="folder-inside" transform="translate(0 1143)">
    <rect x="58" y="46" width="1089" height="815" fill="url(#innerPaper)"/>
    <rect class="inner-texture" x="70" y="170" width="520" height="560" fill="url(#innerWash)" role="img" aria-label="Soft grey background texture"/>
    <rect class="inner-texture" x="613" y="170" width="520" height="560" fill="url(#innerWash)" role="img" aria-label="Soft grey background texture"/>
    <path class="pocket" d="M58 861 H1147 V1134 H660 Q644 1134 639 1112 L601 884 L563 1112 Q558 1134 542 1134 H58 Z" fill="url(#pocketWash)"/>

    <circle cx="198" cy="408" r="44" fill="var(--pink)"/>
    <text class="brand-name" x="258" y="427" fill="var(--blue)">Helix Care</text>
    <circle cx="742" cy="408" r="44" fill="var(--pink)"/>
    <text class="brand-name" x="802" y="427" fill="var(--blue)">Helix Care</text>

    <path d="M184 861 V835 Q184 827 192 827 H459 Q467 827 467 835 V861 Z" fill="var(--pink)"/>
    <text class="tab-url" x="326" y="849" text-anchor="middle">www.helixcaresupply.com</text>
    <path d="M735 861 V835 Q735 827 743 827 H1011 Q1019 827 1019 835 V861 Z" fill="var(--blue)"/>
    <text class="tab-url" x="877" y="849" text-anchor="middle">www.helixcaresupply.com</text>

    <line x1="58" y1="861" x2="601" y2="861" stroke="var(--pink)" stroke-width="4"/>
    <line x1="601" y1="861" x2="1147" y2="861" stroke="var(--blue)" stroke-width="4"/>
    <line class="fold-line" x1="601" y1="46" x2="601" y2="861"/>
    <path class="safe-line" d="M72 60 H1133 V1120 H666 Q652 1120 648 1104 L601 878 L554 1104 Q550 1120 536 1120 H72 Z"/>
    <path class="die-inner" d="M58 46 H1147 V1134 H660 Q644 1134 639 1112 L601 884 L563 1112 Q558 1134 542 1134 H58 Z"/>
    <path class="die-cut" d="M53 41 H1152 V1139 H660 Q640 1139 634 1115 L601 874 L568 1115 Q562 1139 542 1139 H53 Z"/>
  </g>
</svg>
</body>
</html>
```